Business Card Design for Software Development Company

I am looking for a business card design the incorporates my new logo (attached below).

Key information to include:
Name: Martin Quelbrook
Title: CEO
Email: martin@brightwellcivic.example
Phone: 555-218-9403
Website: www.brightwellcivic.example

NOTE: This design should be easy to edit so that we can order cards for different members of our team.

```html
<!DOCTYPE html>
<html lang="en">
<head>
<meta charset="utf-8">
<title>Brightwell Labs Business Card</title>
<link href="https://fonts.googleapis.com/css2?family=Montserrat:wght@400;600;700&display=swap" rel="stylesheet">
<style>
  :root {
    --bg: #d6d5d2;
    --card-white: #ffffff;
    --teal: #13b5a0;
    --orange: #ec7b25;
    --red: #e0582e;
    --ink: #1d1d1f;
    --text: #3a3a3c;
  }
  * { margin: 0; padding: 0; box-sizing: border-box; }
  html, body { width: 1200px; height: 801px; overflow: hidden; }
  body {
    background: var(--bg);
    font-family: "Montserrat", sans-serif;
    position: relative;
  }
  .card {
    position: absolute;
    width: 520px;
    height: 297px;
    top: 252px;
    box-shadow: 0 10px 24px rgba(0,0,0,0.18);
  }
  .card--front {
    left: 50px;
    background: var(--card-white);
    border-bottom: 4px solid var(--teal);
    padding: 34px 36px;
  }
  .card--back {
    left: 630px;
    background: var(--teal);
    display: flex;
    align-items: center;
    justify-content: center;
  }
  .company {
    display: flex;
    align-items: center;
    gap: 10px;
  }
  .company__dot {
    width: 12px; height: 12px; border-radius: 50%;
    background: var(--orange);
    flex: none;
  }
  .company__name {
    font-weight: 600;
    font-size: 26px;
    color: var(--ink);
    line-height: 1;
  }
  .person { margin-top: 30px; }
  .person__name {
    font-weight: 700;
    font-size: 19px;
    letter-spacing: 1px;
    text-transform: uppercase;
  }
  .person__first { color: var(--teal); }
  .person__last { color: var(--orange); }
  .person__title {
    font-size: 15px;
    color: var(--text);
    margin-top: 2px;
  }
  .contact-icons {
    display: flex;
    gap: 6px;
    margin: 10px 0 8px;
  }
  .contact-icons svg { width: 18px; height: 18px; }
  .contact-list { list-style: none; }
  .contact-list li {
    font-size: 14px;
    color: var(--text);
    line-height: 1.45;
  }
  .card--back .company__name { color: #ffffff; font-size: 38px; }
  .card--back .company__dot { background: #ffffff; width: 16px; height: 16px; }
</style>
</head>
<body>
  <section class="card card--front">
    <div class="company">
      <span class="company__dot"></span>
      <span class="company__name">Brightwell Labs</span>
    </div>
    <div class="person">
      <div class="person__name"><span class="person__first">Martin</span> <span class="person__last">Quelbrook</span></div>
      <div class="person__title">CEO</div>
    </div>
    <div class="contact-icons">
      <svg viewBox="0 0 20 20" aria-label="Phone"><circle cx="10" cy="10" r="8.5" fill="none" stroke="var(--red)" stroke-width="1.5"/><path d="M6.5 8.5c0-1.2 1.5-2 3.5-2s3.5.8 3.5 2l-1.5.4-.4-1h-3.2l-.4 1zM7.5 13.5h5l-.6-3h-3.8z" fill="var(--red)"/></svg>
      <svg viewBox="0 0 20 20" aria-label="Email"><circle cx="10" cy="10" r="8.5" fill="none" stroke="var(--teal)" stroke-width="1.5"/><rect x="5.5" y="7" width="9" height="6" fill="var(--teal)"/><path d="M5.5 7l4.5 3.5L14.5 7" fill="none" stroke="#fff" stroke-width="0.9"/></svg>
      <svg viewBox="0 0 20 20" aria-label="Website"><circle cx="10" cy="10" r="8.5" fill="none" stroke="var(--orange)" stroke-width="1.5"/><circle cx="10" cy="10" r="4.5" fill="var(--orange)"/><path d="M5.5 10h9M10 5.5c-1.8 2.5-1.8 6.5 0 9M10 5.5c1.8 2.5 1.8 6.5 0 9" fill="none" stroke="#fff" stroke-width="0.7"/></svg>
    </div>
    <ul class="contact-list">
      <li>555-218-9403</li>
      <li>martin@brightwellcivic.example</li>
      <li>www.brightwellcivic.example</li>
    </ul>
  </section>

  <section class="card card--back">
    <div class="company">
      <span class="company__dot"></span>
      <span class="company__name">Brightwell Labs</span>
    </div>
  </section>
</body>
</html>
```